Modern design company business card design

We are a design oriented construction firm. The owner is an architect and licensed General Contractor and accomplished furniture designer. We do new home construction and large scale remodeling and office design. We would like a design for our new business cards that is clean and modern, but relatable. We like the bright green color of our logo mixed with different shades of grey. We're also open to reinterpreting the logo.

Target Market(s)

Potential design clients,
Construction clients

Industry/Entity Type

Architecture

Contact Information for Business Card

Tall Maple Design | Build Inc. (optional with logo, Inc. optional)Jeffrey MorganOwner (optional)317.555.0148 cell317.431.8056 officejmorgan@greensquareinc.comwww.greensquareinc.com

Font styles to use
Sans Serif
Other font styles liked:
• Avenir

Requirements
Nice to have
• I like designs that have some continuity between the front and back, i.e. similar layouts or graphic elements that wrap around the card. I tend to prefer horizontal over vertical, but that's not a have to. I also tend to prefer white or recycled paper.

```html
<!DOCTYPE html>
<html lang="en">
<head>
<meta charset="utf-8">
<title>Tall Maple Design | Build – Business Cards</title>
<link rel="stylesheet" href="https://fonts.googleapis.com/css2?family=Mulish:wght@300;400;700&display=swap">
<style>
  :root {
    --backdrop: #2e2927;
    --green-light: #c8e070;
    --green-mid: #a3d563;
    --green-deep: #6fc25a;
    --ink-white: #ffffff;
    --card-shadow: rgba(0, 0, 0, 0.45);
  }
  * { box-sizing: border-box; margin: 0; padding: 0; }
  html, body {
    width: 1200px;
    height: 844px;
    overflow: hidden;
    background: var(--backdrop);
    font-family: "Mulish", "Avenir", sans-serif;
    color: var(--ink-white);
  }
  .stage {
    width: 1200px;
    height: 844px;
    display: flex;
    align-items: center;
    justify-content: center;
    gap: 60px;
  }
  .card {
    position: relative;
    width: 520px;
    height: 297px;
    background: linear-gradient(160deg, var(--green-light) 0%, var(--green-mid) 50%, var(--green-deep) 100%);
    box-shadow: 0 14px 30px var(--card-shadow);
  }
  .wordmark {
    font-weight: 300;
    letter-spacing: 0.08em;
    text-transform: uppercase;
    white-space: nowrap;
    color: var(--ink-white);
  }
  .card-back .wordmark {
    position: absolute;
    left: 34px;
    top: 78px;
    font-size: 23px;
  }
  .card-front .wordmark {
    position: absolute;
    left: 50%;
    top: 50%;
    transform: translate(-50%, -50%);
    font-size: 27px;
  }
  .contact {
    position: absolute;
    left: 232px;
    top: 140px;
  }
  .contact-name {
    font-weight: 700;
    font-size: 15px;
    line-height: 1.2;
  }
  .contact-role {
    font-weight: 400;
    font-size: 12px;
    margin-bottom: 14px;
  }
  .contact-list { list-style: none; }
  .contact-list li {
    display: flex;
    align-items: center;
    gap: 10px;
    font-size: 12.5px;
    line-height: 19px;
    font-weight: 400;
  }
  .contact-list svg {
    width: 11px;
    height: 11px;
    fill: none;
    stroke: var(--ink-white);
    stroke-width: 1.6;
    flex: none;
  }
</style>
</head>
<body>
<main class="stage">
  <section class="card card-back" aria-label="Business card back with contact details">
    <div class="wordmark">Tall Maple Design | Build</div>
    <div class="contact">
      <p class="contact-name">Dennis Holloway</p>
      <p class="contact-role">Owner</p>
      <ul class="contact-list">
        <li>
          <svg viewBox="0 0 12 12" aria-hidden="true"><path d="M2 1.5 L4 1.5 L5 4 L3.8 5 Q5 7.5 7 8.2 L8 7 L10.5 8 L10.5 10 Q6 11 3 7.5 Q1 5 2 1.5 Z" fill="var(--ink-white)" stroke="none"/></svg>
          <span>317.555.0172</span>
        </li>
        <li>
          <svg viewBox="0 0 12 12" aria-hidden="true"><rect x="3" y="1" width="6" height="10" rx="1"/><line x1="5.2" y1="9.3" x2="6.8" y2="9.3"/></svg>
          <span>317.555.0148</span>
        </li>
        <li>
          <svg viewBox="0 0 12 12" aria-hidden="true"><rect x="1" y="2.5" width="10" height="7" fill="var(--ink-white)" stroke="none"/><path d="M1 2.8 L6 6.8 L11 2.8" stroke="var(--green-mid)" stroke-width="1.2"/></svg>
          <span>dholloway@tallmapleinc.example</span>
        </li>
        <li>
          <svg viewBox="0 0 12 12" aria-hidden="true"><path d="M5 7 L7 5"/><path d="M4.3 5.6 L2.6 7.3 A1.8 1.8 0 0 0 5.1 9.8 L6.8 8.1"/><path d="M7.7 6.4 L9.4 4.7 A1.8 1.8 0 0 0 6.9 2.2 L5.2 3.9"/></svg>
          <span>www.tallmapleinc.example</span>
        </li>
      </ul>
    </div>
  </section>
  <section class="card card-front" aria-label="Business card front">
    <div class="wordmark">Tall Maple Design | Build</div>
  </section>
</main>
</body>
</html>
```